New Business Card

Need new business cards like attached. if possible add QR code. Vertical Business Card

I need creative and unique business card design using my company logo. Ok to change logo color. We are a small brokerage doing both Real Estate and Mortgage services. Need to have the follow on business card;
1. agent name - Nola Brenner - Realtor
2. cell - 949-555-2146
3. license number - DRE 07461392
4. business name - Tallow Ridge Realty & Lending, Inc
5. business office - 626-555-4817
6. business address - 482 W. Larkmoor Ave #212, Arcadia CA 91006
7. business logo - attached (ok to use different color on logo)

```html
<!DOCTYPE html>
<html lang="en">
<head>
<meta charset="utf-8">
<title>Tallow Ridge Realty &amp; Lending – Business Card</title>
<link rel="stylesheet" href="https://fonts.googleapis.com/css2?family=Roboto:ital,wght@0,400;0,500;1,400;1,700&display=swap">
<style>
  :root {
    --stage: #232323;
    --card-dark: #1f1f24;
    --brand-blue: #2b55be;
    --sky-light: #6cc3ee;
    --sky-mid: #2e9ad8;
    --sky-deep: #2a5fb3;
    --ink-white: #f4f6fa;
  }
  * { box-sizing: border-box; margin: 0; padding: 0; }
  html, body { width: 1200px; height: 780px; overflow: hidden; background: var(--stage); }
  body { font-family: "Roboto", Arial, sans-serif; position: relative; }

  .card {
    position: absolute;
    top: 90px;
    width: 354px;
    height: 600px;
    border-radius: 30px;
    overflow: hidden;
    box-shadow: 0 18px 40px rgba(0,0,0,.55);
  }
  .card--front { left: 190px; }
  .card--back  { left: 656px; background: var(--card-dark); }

  .front-pattern {
    position: absolute; inset: 0;
    background: linear-gradient(160deg, var(--sky-light) 0%, var(--sky-mid) 45%, var(--sky-deep) 100%);
  }
  .front-mark {
    position: absolute; left: 50%; bottom: 120px; transform: translateX(-50%);
    display: flex; align-items: center; gap: 8px;
  }
  .front-mark__square { width: 18px; height: 18px; background: var(--ink-white); }
  .front-mark__name {
    font-weight: 500; font-size: 15px; letter-spacing: 3px; color: var(--ink-white);
  }

  .back-content {
    position: absolute; inset: 0;
    display: flex; flex-direction: column; align-items: center;
    text-align: center; padding-top: 58px;
  }
  .brand-square { width: 110px; height: 110px; background: var(--brand-blue); }
  .brand-name {
    margin-top: 28px;
    font-weight: 500; font-size: 30px; letter-spacing: 9px; color: var(--brand-blue);
    padding-left: 9px;
  }
  .brand-sub {
    margin-top: 6px;
    font-weight: 500; font-size: 12px; letter-spacing: 3px; color: var(--brand-blue);
  }
  .agent-name {
    margin-top: 54px;
    font-style: italic; font-weight: 700; font-size: 22px; color: var(--brand-blue);
    text-transform: uppercase;
  }
  .agent-role { font-style: italic; font-size: 18px; color: var(--ink-white); margin-top: 2px; }
  .rule { width: 54px; height: 2px; background: var(--brand-blue); margin: 14px 0; }
  .phone { font-style: italic; font-size: 18px; color: var(--ink-white); line-height: 1.3; }
  .company { font-style: italic; font-size: 17px; color: var(--brand-blue); }
  .address { font-style: italic; font-size: 16px; color: var(--ink-white); line-height: 1.35; margin-top: 4px; }
  .license { font-size: 17px; color: var(--ink-white); }
  .license__label { color: var(--brand-blue); font-style: italic; }
</style>
</head>
<body>
  <section class="card card--front">
    <div class="front-pattern" role="img" aria-label="Repeating tiled pattern of the company mark in light and deep blue"></div>
    <div class="front-mark">
      <span class="front-mark__square"></span>
      <span class="front-mark__name">TALLOW RIDGE</span>
    </div>
  </section>

  <section class="card card--back">
    <div class="back-content">
      <div class="brand-square"></div>
      <div class="brand-name">TALLOW RIDGE</div>
      <div class="brand-sub">REALTY AND LENDING, INC</div>

      <div class="agent-name">Nola Brenner</div>
      <div class="agent-role">Realtor</div>
      <div class="rule"></div>
      <div class="phone">949-555-2146</div>
      <div class="phone">626-555-4817</div>
      <div class="rule"></div>
      <div class="company">Tallow Ridge Realty &amp; Lending, Inc</div>
      <div class="address">482 W. Larkmoor Ave #212,<br>Arcadia CA 91006</div>
      <div class="rule"></div>
      <div class="license"><span class="license__label">LIC</span> DRE 07461392</div>
    </div>
  </section>
</body>
</html>
```